Creative Web Design for an ERP (technology) Consulting Business

I need two pages designed for the ERP Project Management Consulting Company I am starting. One page is the home page, the other page is an important inside page.

I've looked at many different templates for sites like this, and they all look the same to me. I am working with PixelGuild designers because I want something unique.

This site will be implemented with Wordpress using the Elementor framework,

About Me ---
I have worked with PixelGuild several times before, and I have tired to do everything I can to ve helpful. In the uploads, you will find PDF's with wireframes outlning the layout of the pages, as well as explanatios for each section. There are Word documents that you can copy into text. The list below explains the files included.

Although the wireframes suggest a layout, please feel free to use your creativity - often, I find that the designs I like the most are designs I have never thought of.

About the Company --
ERP (Enterprise Resource Planning) systems are business computer systems that tie different businesss functions together. These systems are expensive and complicated, and efforts to implement them often fail. The purpose of the company is to increase the chance of success by focusing on the things that need to be right.

I have uploaded several files to help clarify what I am looking for:
• 1a - Home Page Wireframe - PDF
Wireframe for the home page with an explanation of each section.
• 1b - Home Page Text – Word
A Word document so that you can copy the text.
• 2 - Copper Harbor Logo – ZIP
Four different versions of the company logo in Adobe Illustrator, PNG, and JPG formats. Any of the four are acceptable:
1. Logo_1 – Black on Transparent – Same Line ERP
2. Logo_2 – White on Transparent – Same Line ERP
3. Logo_3 – Black on Transparent – Big ERP on Different Line
4. Logo_4 – White on Transparent – Big ERP on Different Line
• 3a - Copper Harbor Page Wireframe – PDF
Wireframe for he Copper Harbor page, with explanations and a detailed breakdown of the top section.
• 3b - Copper Harbor Text – Word
• 4 - Colors and Palettes – PDF
• 5 - Change Management Icon – EPS
• 6 – Site Map
If you wish to see it, the site map provides an idea of the entire site. The two pages circled in red are the ones I need to be designed.

Thank you for your interest in this project!

Target Market(s)

Corporate decision makers, primarily CIOs and CFOs, as well as ERP project managers and influencers.

Industry/Entity Type

Consulting

Number of Pages Required

2 page

Font styles to use
Sans Serif

Requirements
Must have
• Pages that contain the elements explained on the wireframes provided.
Nice to have
• A design that looks and feels unique
Should not have
• A typical, template layour

```html
<!DOCTYPE html>
<html lang="en">
<head>
<meta charset="utf-8">
<title>Change Management – Copper Harbor ERP</title>
<link href="https://fonts.googleapis.com/css2?family=Outfit:wght@300;400;500;600&display=swap" rel="stylesheet">
<style>
:root{
  --blue:#0b63c9;
  --purple:#5b2d8e;
  --orange:#f26c22;
  --ink:#111418;
  --muted:#7d7d84;
  --footer:#0b0b0d;
}
*{margin:0;padding:0;box-sizing:border-box}
html,body{width:1200px;height:3970px;overflow:hidden}
body{position:relative;background:#fff;font-family:"Outfit",sans-serif;color:var(--ink)}
.abs{position:absolute}
.site-header{position:absolute;top:0;left:0;width:1200px;height:62px;background:#fff;z-index:5}
.brand{position:absolute;left:90px;top:19px;display:flex;align-items:center;gap:9px}
.brand-dot{width:22px;height:22px;border-radius:50%;background:var(--ink)}
.brand-name{font-weight:600;font-size:19px;line-height:1}
.nav{position:absolute;top:24px;left:0;font-size:12px;color:#444}
.nav span{position:absolute;white-space:nowrap}
.nav .active{color:var(--ink);font-weight:500}
.nav .active::after{content:"";position:absolute;left:0;right:0;top:38px;height:2px;background:var(--blue)}
.contact-btn{position:absolute;left:995px;top:13px;width:116px;height:36px;border:1.5px solid var(--blue);border-radius:18px;color:var(--blue);font-size:12px;font-weight:500;display:flex;align-items:center;justify-content:center}
.hero-bg{position:absolute;top:62px;left:0;width:1200px;height:390px;background:linear-gradient(180deg,#dfe1e4,#eceef0)}
.hero-icon{position:absolute;left:568px;top:115px;width:64px;height:64px;border-radius:50%;background:#fff;box-shadow:0 4px 14px rgba(0,0,0,.1)}
.hero-icon::after{content:"";position:absolute;left:22px;top:22px;width:20px;height:20px;border-radius:50%;background:var(--ink)}
.hero-title{position:absolute;top:188px;width:1200px;text-align:center;font-size:47px;font-weight:500}
.tab{position:absolute;top:328px;width:208px;height:60px;background:#fff;border-radius:8px;box-shadow:0 6px 18px rgba(0,0,0,.08);display:flex;align-items:center;justify-content:center;font-size:16px;color:#444}
.tab.active{border:2px solid var(--blue);color:var(--ink);font-weight:500;font-size:15px}
h2{font-weight:500;color:var(--ink)}
.body-text{font-size:13px;line-height:20px;color:var(--muted);font-weight:300}
.list{list-style:none;font-size:13px;color:var(--muted);font-weight:300}
.list li{position:relative;padding-left:14px;height:26.5px}
.list li::before{content:"";position:absolute;left:0;top:7px;width:4px;height:4px;border-radius:50%;background:var(--ink)}
.list b{font-weight:500;color:var(--ink)}
.label{font-size:13px;font-weight:500;color:var(--ink)}
.watch{position:absolute;display:flex;align-items:center;font-size:12px;color:var(--ink)}
.watch .play{width:34px;height:34px;border:1.5px solid var(--ink);border-radius:50%;display:flex;align-items:center;justify-content:center}
.watch .line{width:26px;height:1px;background:var(--ink);margin:0 8px}
.photo{position:absolute;border-radius:16px}
.badge{position:absolute;width:86px;height:86px;border-radius:50%;background:#fff;box-shadow:0 4px 14px rgba(0,0,0,.1);display:flex;align-items:center;justify-content:center}
.badge::after{content:"";width:22px;height:22px;border-radius:50%;background:var(--ink)}
.footer-col h4{font-size:16px;font-weight:500;color:#fff;margin-bottom:16px}
.footer-col{position:absolute;top:3625px;color:#d9d9dd;font-size:11.5px;line-height:22px}
.footer-brand{position:absolute;left:86px;top:3640px;display:flex;align-items:center;gap:10px;color:#fff;font-size:16px;font-weight:500}
.footer-brand .mark{width:28px;height:28px;border-radius:50%;background:#fff}
.email-field{border-bottom:1px solid #555;width:188px;padding:14px 4px 6px;font-size:9px;letter-spacing:1.5px;color:#aaa}
.sub-btn{margin-top:22px;width:186px;height:38px;border-radius:19px;background:var(--blue);color:#fff;font-size:12px;font-weight:500;display:flex;align-items:center;justify-content:center}
.copyright{position:absolute;left:88px;top:3914px;font-size:11.5px;color:#ddd}
.social{position:absolute;top:3912px;width:14px;height:14px;border-radius:50%;border:1.5px solid #fff}
</style>
</head>
<body>

<header class="site-header">
  <div class="brand">
    <div class="brand-dot"></div>
    <div class="brand-name">COPPER HARBOR ERP</div>
  </div>
  <nav class="nav">
    <span style="left:430px">Home</span>
    <span style="left:493px">About</span>
    <span style="left:560px">Services</span>
    <span class="active" style="left:630px">Core Pillars</span>
    <span style="left:715px">Adaptive Method</span>
    <span style="left:828px">Resources</span>
    <span style="left:905px">Case Studies</span>
  </nav>
  <div class="contact-btn">Contact Us</div>
</header>

<section class="hero">
  <div class="hero-bg" role="img" aria-label="Faded photo of a whiteboard with sketched communication and idea icons"></div>
  <svg class="abs" style="left:0;top:250px" width="1200" height="210" viewBox="0 0 1200 210">
    <path d="M0,210 L0,60 C200,160 420,170 620,160 C820,150 1000,140 1200,175 L1200,210Z" fill="#fff"/>
    <path d="M0,60 C200,160 420,170 620,160 C820,150 1000,140 1200,175" fill="none" stroke="var(--blue)" stroke-width="3"/>
  </svg>
  <div class="hero-icon"></div>
  <h1 class="hero-title">Change Management</h1>
  <div class="tab" style="left:-58px">Functionality</div>
  <div class="tab" style="left:160px">Technology</div>
  <div class="tab" style="left:376px">Best Quality</div>
  <div class="tab active" style="left:594px">Change Management</div>
  <div class="tab" style="left:810px">Governance</div>
  <div class="tab" style="left:1028px">Overview</div>
</section>

<section class="why">
  <h2 class="abs" style="left:124px;top:540px;font-size:40px">Why</h2>
  <p class="abs body-text" style="left:124px;top:598px;width:452px">If people cannot, or will not, use the system, it will fail. A well established model explains intrinsic motivation. Learning this model was a pivotal insight for me. I realized that ERP implementations almost always inadvertently ignore these three needs:</p>
  <ul class="abs list" style="left:126px;top:696px">
    <li><b>Autonomy,</b> the need for independence.</li>
    <li style="margin-top:4px"><b>Competence,</b> the need to feel you are good at what you do.</li>
    <li style="margin-top:4px"><b>Relatedness,</b> the need to feel connected to other people.</li>
  </ul>
  <div class="watch" style="left:120px;top:804px"><div class="play"><svg width="10" height="10" viewBox="0 0 10 10"><path d="M2 1 L9 5 L2 9Z" fill="#111418"/></svg></div><div class="line"></div>Watch Video</div>
  <div class="photo" style="left:649px;top:499px;width:415px;height:355px;background:linear-gradient(135deg,#2f3b4a,#6f7e8c 60%,#b9c2c9)" role="img" aria-label="Hands of a team joining jigsaw puzzle pieces together"></div>
  <div class="abs" style="left:597px;top:538px;width:23px;height:23px;border-radius:50%;background:var(--orange)"></div>
  <div class="abs" style="left:1092px;top:782px;width:33px;height:33px;border-radius:50%;background:var(--purple)"></div>
</section>

<section class="how">
  <h2 class="abs" style="left:0;top:933px;width:1200px;text-align:center;font-size:42px">How Change Management Work</h2>
  <p class="abs body-text" style="left:260px;top:994px;width:680px;text-align:center">Change management frameworks, such as the Lindqvist Model, Harlow's Model, and Vantor's STAGE. models are vastly better than nothing. They can work as long as you don't ignore why they work and end up stepping on your own feet.</p>
  <p class="abs body-text" style="left:260px;top:1076px;width:680px;text-align:center">The Copper Harbor model is based on the basic psychological needs spelled out by self-determination theory: <b style="color:var(--ink);font-weight:500">autonomy, competence,</b> and <b style="color:var(--ink);font-weight:500">relatedness.</b></p>
  <div class="photo" style="left:151px;top:1157px;width:898px;height:389px;border-radius:14px;background:linear-gradient(120deg,#2a3038,#55606a 50%,#3a4048);box-shadow:0 14px 30px rgba(0,0,0,.18)" role="img" aria-label="Video still of colleagues collaborating around a meeting table"></div>
  <svg class="abs" style="left:566px;top:1318px" width="68" height="68" viewBox="0 0 68 68"><circle cx="34" cy="34" r="31" fill="none" stroke="#fff" stroke-width="3"/><path d="M27 22 L48 34 L27 46Z" fill="#fff"/></svg>
</section>

<section class="pillar">
  <div class="photo" style="left:145px;top:1706px;width:444px;height:537px;background:linear-gradient(160deg,#7a5a3a,#b08a62 50%,#4a4e58)" role="img" aria-label="Woman working with a laptop and notes at a wooden table"></div>
  <h2 class="abs" style="left:653px;top:1758px;font-size:34px">Enabling Autonomy</h2>
  <p class="abs body-text" style="left:655px;top:1816px;width:390px">ERP implementations usually diminish autonomy; starting off on the wrong foot from day one.</p>
  <p class="abs label" style="left:654px;top:1876px">To address avoid this, create:</p>
  <ul class="abs list" style="left:654px;top:1908px">
    <li>Meaningful Participation in every phase.</li>
    <li>Ownership.</li>
    <li>Decentralized Decisions.</li>
    <li>Flexibility.</li>
  </ul>
  <p class="abs label" style="left:654px;top:2022px">ERP implementations often implicitly say:</p>
  <ul class="abs list" style="left:654px;top:2054px">
    <li>Here's how you must do things now.</li>
    <li>We didn't think it was worth asking you.</li>
  </ul>
  <div class="watch" style="left:652px;top:2127px"><div class="play"><svg width="10" height="10" viewBox="0 0 10 10"><path d="M2 1 L9 5 L2 9Z" fill="#111418"/></svg></div><div class="line"></div>Watch Video</div>
</section>

<section class="pillar">
  <div class="photo" style="left:578px;top:2228px;width:444px;height:537px;background:linear-gradient(160deg,#e8e6e2,#c9b9a4 55%,#9a8a78)" role="img" aria-label="Young woman sitting at a desk with coffee cups and notes"></div>
  <div class="badge" style="left:537px;top:2187px"></div>
  <h2 class="abs" style="left:145px;top:2303px;font-size:34px">Fostering Competence</h2>
  <p class="abs body-text" style="left:147px;top:2361px;width:380px">ERP implementations usually diminish autonomy; starting off on the wrong foot from day one.</p>
  <p class="abs label" style="left:146px;top:2421px">To address avoid this:</p>
  <ul class="abs list" style="left:146px;top:2453px">
    <li>Create psychological safety.</li>
    <li>Provide training from day one.</li>
    <li>Focus on feedback.</li>
    <li>Celebrate step-by-step Mastery.</li>
    <li>Provide adequate support.</li>
  </ul>
  <p class="abs label" style="left:146px;top:2593px">ERP implementations implicitly say:</p>
  <ul class="abs list" style="left:146px;top:2625px">
    <li>You're not competent.</li>
  </ul>
  <div class="watch" style="left:144px;top:2667px"><div class="play"><svg width="10" height="10" viewBox="0 0 10 10"><path d="M2 1 L9 5 L2 9Z" fill="#111418"/></svg></div><div class="line"></div>Watch Video</div>
</section>

<section class="pillar">
  <div class="photo" style="left:145px;top:2752px;width:444px;height:581px;background:linear-gradient(170deg,#f2f2f2,#c9a98a 45%,#6d5a4c)" role="img" aria-label="Group of colleagues stacking hands together, seen from below"></div>
  <div class="badge" style="left:537px;top:2722px"></div>
  <h2 class="abs" style="left:653px;top:2820px;font-size:34px">Building Relationships</h2>
  <p class="abs body-text" style="left:655px;top:2878px;width:390px">ERP implementations usually diminish autonomy; starting off on the wrong foot from day one.</p>
  <p class="abs label" style="left:654px;top:2938px">You Can Fix it :</p>
  <ul class="abs list" style="left:654px;top:2970px">
    <li>Understand Organizational Dynamics.</li>
    <li>Create Open, Transparent, Communication.</li>
    <li>Build Relationships and Trust.</li>
    <li>Use Ethical Influence.</li>
    <li>Build a Broad Team.</li>
  </ul>
  <p class="abs label" style="left:654px;top:3111px">ERP implementations often ignore:</p>
  <ul class="abs list" style="left:654px;top:3143px">
    <li>The power of 'likeability'.</li>
    <li>Influence vs authority.</li>
    <li>Informal teams.</li>
    <li>The value of communication.</li>
  </ul>
  <div class="watch" style="left:652px;top:3263px"><div class="play"><svg width="10" height="10" viewBox="0 0 10 10"><path d="M2 1 L9 5 L2 9Z" fill="#111418"/></svg></div><div class="line"></div>Watch Video</div>
</section>

<footer class="site-footer">
  <svg class="abs" style="left:0;top:3400px" width="1200" height="570" viewBox="0 0 1200 570">
    <path d="M0,70 C260,130 520,110 760,80 C940,58 1080,70 1200,110 L1200,570 L0,570Z" fill="var(--footer)"/>
    <path d="M0,56 C260,116 520,96 760,66 C940,44 1080,56 1200,96" fill="none" stroke="var(--blue)" stroke-width="3"/>
  </svg>
  <div class="footer-brand">
    <div class="mark"></div>
    <div>Copper Harbor ERP</div>
  </div>
  <div class="footer-col" style="left:281px">
    <h4>ERP Tools</h4>
    <div>› Copper Harbor</div><div>› Adaptive Method</div><div>› Tools and Resources</div>
  </div>
  <div class="footer-col" style="left:472px">
    <h4>Services</h4>
    <div>› About</div><div>› Project Planning</div><div>› Project Management</div>
    <div style="line-height:14px;margin:4px 0">› Project Assessment<br>&nbsp;&nbsp;&nbsp;and Turnaround</div>
    <div>› Change Management</div>
  </div>
  <div class="footer-col" style="left:665px">
    <h4>Contact Us</h4>
    <div style="display:flex;align-items:center;gap:12px;font-size:13px;color:#fff;text-decoration:underline">
      <svg width="16" height="12" viewBox="0 0 16 12"><rect x=".75" y=".75" width="14.5" height="10.5" fill="none" stroke="#fff" stroke-width="1.2"/><path d="M1 1 L8 7 L15 1" fill="none" stroke="#fff" stroke-width="1.2"/></svg>info@copperharborerp
    </div>
    <div style="display:flex;align-items:center;gap:12px;font-size:13px;color:#fff;margin-top:28px">
      <svg width="16" height="16" viewBox="0 0 16 16"><path d="M3 1.5 L6 1.5 L7 5 L5 6.5 C6 9 7 10 9.5 11 L11 9 L14.5 10 L14.5 13 C14.5 14 13.5 14.5 12.5 14.5 C6.5 14 2 9.5 1.5 3.5 C1.5 2.5 2 1.5 3 1.5Z" fill="none" stroke="#fff" stroke-width="1.1"/></svg>(555) 014-2280
    </div>
  </div>
  <div class="footer-col" style="left:901px">
    <h4>Subscribe for Updates</h4>
    <div style="line-height:15px;width:210px;color:#fff;font-size:11px">Subscribe and be the first to receive all the latest insights.</div>
    <div class="email-field">EMAIL</div>
    <div class="sub-btn">Subscribe</div>
  </div>
  <div class="abs" style="left:0;top:3880px;width:1200px;height:1px;background:#222"></div>
  <div class="copyright">2024 Copyright © Harborline All Rights Reserved.</div>
  <div class="social" style="left:1008px" aria-label="Social link"></div>
  <div class="social" style="left:1049px" aria-label="Social link"></div>
  <div class="social" style="left:1091px" aria-label="Social link"></div>
</footer>

</body>
</html>
```